Wordpress Theme for Harbourline Clinics

** Please view updated Sitemap2.pdf doc to clarify some confusion ***

This is a multiuser WordPress subscription site for Harbourline Clinics. Please see attachment for sitemap. Please do not include extra content like social media icons, search bars, or images. If you have questions, please ask for clarification.
The site contains the following pages and sub-pages:

1. Home
2. Our Clinic
2a. Our Clinic > Mission
2b. Our Clinic > Services
2c. Our Clinic > Clinic Policies
2d. Our Clinic > Schedules
3. Our Staff
3a. Our Staff > [Staff member page]
4. Resources
4a. Resources > Patient Health (index)
4b. Resources > Patient Health (index) > [post]
4c. Resources > Links
4d. Resources > Forms
5. Alerts
5a. Alerts > [Alert Page]
6. Contact Us

Includes the Following Pages, Subpages, and Content
1. Home
a. About Us
b. Our Staff
c. Bulletins
d. Accepting New Patients (shown as an alert widget)
e. Links
i. Physician Toolbox
ii. Book an Appointment
f. Clinic Policies
i. Show first 3 policies (e.g. Late Arrivals, Missed Appointments, Fees)
ii. Link to Clinic Policies page
g. Primary widget (displayed on all pages)
i. Hours of operation
ii. Contact Info
1. Tel
2. Fax
3. Email
4. Address
5. Get directions (link to Google Maps)
2. Our Clinic
a. Main Page
i. Clinic Name
ii. Overview
iii. Languages Spoken
iv. Secondary Navigation
1. Mission
2. Services
3. Clinic Policies
4. Schedules (see attachment)
b. Our Clinic > Mission
c. Our Clinic > Services
i. For each service include service TITLE and DESCRIPTION
d. Our Clinic > Clinic Policies
i. For each policy include policy TITLE and DESCRIPTION
ii. Include the following policies in mockup
1. Late arrivals
2. Missed appointments
3. Fees for missed appointments
4. Referrals and follow-ups
5. Services not covered by RDA
6. Information for LTF patients
7. Medical Legal Reports
e. Our Clinic > Schedules
3. Our Staff
a. Main Page
i. Display a list of staff members. Include NAME and DESIGNATION
b. Our Staff > [Staff Name]
i. Include NAME, PICTURE, DESIGNATION, and BIO
4. Resources
a. Resources > Patient Health
i. Main Page
1. Posts (ordered by date)
a. Title
b. Summary
2. Side Navigation
a. Post Categories
ii. Patient Health > [post title]
1. Title
2. Post Category
3. Date
4. Author
5. Summary
6. Body
b. Resources > Links
1. Secondary Navigation - Categories
a. Sample Categories:
i. Local Services
ii. RDA and Drug Coverage
iii. Mental Health Resources
2. Category page
a. Include the following links in the 'Local Services' category
i. Hypertension clinics
ii. Home Care services
iii. Vaccine Clinics
c. Resources > Forms
i. Display a table with form TITLE and CATEGORY
ii. Side Navigation
1. Form Categories
a. Use the following sample Categories
i. Referrals
ii. Insurance
iii. Intake
iv. Discharge
v. Waivers
5. Alerts
a. Main page
i. List of all Alert posts
1. Include post TITLE as a link to the post
ii. Side Navigation
1. Alerts Archive
a. shown as Month + Number of posts
iii. Alerts > [Alert page]
1. Include TITLE, DATE, AUTHOR, BODY
6. Contact Us
a. Map
b. Hours of operation
c. Address
d. Phone number
e. Fax number
e. Fax number
f. Map
g. Email

Design notes:
- fixed width
- responsive (need designs for mobile, tablet, and desktop)
- simple, dark font, white background
- use Font Awesome icons where needed
- user adds own logo

Target Market(s)

Harbourline Clinics

Industry/Entity Type

Medical

Number of Pages Required

5+ page

Font styles to use
Serif
Sans Serif

Requirements
Must have
• Please keep designs very simple.
• Examples:
• https://www.quolbin.com/install
• http://www.ventrohax.com/company/about-us
• http://brindlequota.org/
• http://www.trosk.com/
Should not have
• Minimal or no use of shadows and gradients

```html
<!DOCTYPE html>
<html lang="en">
<head>
<meta charset="utf-8">
<title>Our Staff – Harbourline Clinics</title>
<link href="https://fonts.googleapis.com/css2?family=Open+Sans:wght@400;600;700&display=swap" rel="stylesheet">
<style>
:root{
  --blue:#0a8de3;
  --ink:#222;
  --text:#333;
  --muted:#777;
  --band:#f7f7f7;
  --photo:#f5f5f5;
  --border:#cfcfcf;
  --footer:#262626;
  --footer-text:#8c8c8c;
  --footer-head:#9a9a9a;
  --white:#fff;
}
*{box-sizing:border-box;margin:0;padding:0}
html,body{width:1200px;height:1148px;overflow:hidden;background:var(--white)}
body{position:relative;font-family:"Open Sans",Arial,sans-serif;color:var(--text)}
a{color:inherit;text-decoration:none}
.abs{position:absolute}

.topbar{left:0;top:0;width:1200px;height:30px;background:var(--blue);color:var(--white);font-size:9.5px}
.topbar .contact{left:161px;top:9px}
.topbar .contact span+span{border-left:1px solid var(--white);margin-left:5px;padding-left:5px}
.topbar .links{right:161px;top:9px}
.topbar .links a+a{border-left:1px solid var(--white);margin-left:6px;padding-left:6px}

.header{left:0;top:30px;width:1200px;height:83px}
.brand{left:162px;top:22px;display:flex;align-items:center;gap:12px}
.brand-dot{width:30px;height:30px;border-radius:50%;background:var(--blue)}
.brand-name{font-size:21px;font-weight:600;color:var(--ink)}
.nav{left:0;top:0}
.nav a{position:absolute;top:0;height:83px;line-height:83px;font-size:11px;color:var(--text);text-align:center}
.nav a.active{background:var(--blue);color:var(--white)}

.pagehead{left:0;top:113px;width:1200px;height:59px;background:var(--band)}
.pagehead h1{position:absolute;left:162px;top:16px;font-size:10px;font-weight:700;color:var(--ink)}
.pagehead .crumbs{position:absolute;left:162px;top:35px;font-size:9.5px;color:var(--ink)}

.profile-photo{left:161px;top:210px;width:428px;height:300px;background:linear-gradient(#f6f6f6,#ededed);border-bottom:4px solid var(--blue)}
.profile{left:610px;top:208px;width:429px}
.profile h2{font-size:12.5px;font-weight:600;color:var(--ink);padding-bottom:10px;border-bottom:1px solid var(--border);width:114px}
.profile .role{margin-top:11px;font-size:9px;font-weight:700;color:var(--ink)}
.profile .bio{margin-top:16px;font-size:9.6px;line-height:15px;text-align:justify}
.profile h3{margin-top:25px;font-size:9.5px;font-weight:700;color:var(--ink)}
.profile .hours{margin-top:9px;font-size:9.6px}

.staff-card{top:555px;width:203px;height:241px}
.staff-card .photo{height:188px;background:linear-gradient(#f7f7f7,#eeeeee)}
.staff-card .caption{height:53px;border:1px solid var(--border);padding:9px 7px}
.staff-card .name{font-size:12px;font-weight:600;color:#444}
.staff-card .dept{font-size:10.5px;color:var(--blue);margin-top:2px}

.footer{left:0;top:922px;width:1200px;height:226px;background:var(--footer);border-top:4px solid var(--blue);color:var(--footer-text);font-size:9.5px}
.footer .brand{top:36px;left:162px}
.footer .brand-name{color:var(--white)}
.footer .about{position:absolute;left:162px;top:86px;width:205px;line-height:13.5px;color:#cfcfcf;font-size:8.5px}
.footer h4{position:absolute;top:34px;font-size:12px;font-weight:600;color:var(--footer-head)}
.footer ul{position:absolute;top:58px;list-style:none;line-height:18px}
.footer ul li:first-child.on{color:#bdbdbd}
.footer dl{position:absolute;left:838px;top:58px;display:grid;grid-template-columns:89px 120px;line-height:15px}
.footer .legal{position:absolute;left:0;top:188px;width:1200px;border-top:1px solid #444;height:38px}
.footer .legal span{position:absolute;top:10px}
</style>
</head>
<body>

<div class="abs topbar">
  <div class="abs contact"><span>To help Here : 000 555 0199</span><span>Email : hello@harbourline.test</span></div>
  <div class="abs links"><a href="#">Book an Appointment</a><a href="#">Physician Toolbox</a></div>
</div>

<header class="abs header">
  <div class="abs brand"><span class="brand-dot"></span><span class="brand-name">Harbourline Clinics</span></div>
  <nav class="abs nav">
    <a href="#" style="left:560px;width:50px">Home</a>
    <a href="#" style="left:633px;width:58px">Our Clinic</a>
    <a href="#" style="left:720px;width:64px">Newsletter</a>
    <a href="#" class="active" style="left:811px;width:60px">Our Staff</a>
    <a href="#" style="left:895px;width:60px">Resources</a>
    <a href="#" style="left:983px;width:60px">Contact Us</a>
  </nav>
</header>

<section class="abs pagehead">
  <h1>OUR STAFF</h1>
  <div class="crumbs">HOME / OUR STAFF/STAFF-MEMBER</div>
</section>

<div class="abs profile-photo" role="img" aria-label="Portrait photo of Dr. Elena Varga in a white coat with a stethoscope"></div>
<article class="abs profile">
  <h2>Dr. Elena Varga</h2>
  <p class="role">PEDIATRIST</p>
  <p class="bio">Contrary to popular belief, Lorem Ipsum is not simply random text. It has roots in a piece of classical Latin literature from 45 BC, making it over 2000 years old. Edwin Marlowe, a Latin professor at Ashgrove College in Norland, looked up one of the more obscure Latin words, consectetur, from a Lorem Ipsum passage, and going through the cites of the word in classical literature.</p>
  <h3>Office Hours</h3>
  <p class="hours">Monday, Thursday, Friday</p>
</article>

<div class="abs staff-card" style="left:161px">
  <div class="photo" role="img" aria-label="Portrait photo of Dr. Elena Varga"></div>
  <div class="caption"><div class="name">Dr. Elena Varga</div><div class="dept">Pediatric Clinic</div></div>
</div>
<div class="abs staff-card" style="left:386px">
  <div class="photo" role="img" aria-label="Portrait photo of Dr. Owen Petrak"></div>
  <div class="caption"><div class="name">Dr. Owen Petrak</div><div class="dept">Cardiac Clinic</div></div>
</div>
<div class="abs staff-card" style="left:611px">
  <div class="photo" role="img" aria-label="Portrait photo of Dr. Mira Solberg in scrubs"></div>
  <div class="caption"><div class="name">Dr. Mira Solberg</div><div class="dept">Rehabilitation Therapy</div></div>
</div>
<div class="abs staff-card" style="left:836px">
  <div class="photo" role="img" aria-label="Portrait photo of Dr. Tomas Hale"></div>
  <div class="caption"><div class="name">Dr. Tomas Hale</div><div class="dept">Laryngological Clinic</div></div>
</div>

<footer class="abs footer">
  <div class="abs brand"><span class="brand-dot"></span><span class="brand-name">Harbourline Clinics</span></div>
  <p class="about">Lorem Ipsum is simply dummy text of the printing and typesetting industry. Lorem Ipsum has been the industry's standard dummy text</p>

  <h4 style="left:461px">Navigation</h4>
  <ul style="left:461px"><li class="on">Home</li><li>Our Clinic</li><li>Newsletter</li><li>Our Staff</li><li>Resources</li></ul>

  <h4 style="left:686px">Links</h4>
  <ul style="left:686px"><li>Help</li><li>Support</li><li>Privacy Policy</li></ul>

  <h4 style="left:836px">Contact Us</h4>
  <dl>
    <dt>Telephone :</dt><dd>000-555-0142</dd>
    <dt>Email:</dt><dd>info@harbourline.test</dd>
    <dt>Address:</dt><dd>48 Quay Lane<br>Port Elden, Northshire,<br>N0R 7QX</dd>
  </dl>

  <div class="legal">
    <span style="left:162px">© 2015 Harbourline Clinics. All Rights Reserved</span>
    <span style="left:463px">About Us</span>
    <span style="left:530px">Terms of Use</span>
    <span style="left:615px">Privacy Policy</span>
    <span style="right:164px">Site design &amp; developed by Fernpoint Web Studio</span>
  </div>
</footer>

</body>
</html>
```